Business Cards Design for the electrical wholesaler: clean bold dynamic :)

We need a business card design that would follow our latest brand guidelines. As an electrical wholesaler we want to bring a fresh look and feel into the industry. The design should be clean bold and dynamic. It should come alive with the renewed energy of our green colour. Our grey colour should keep things balanced and complement the notion of maturity and responsibility. We employ Lato as a corporate font however are not bound by this font and we’re open to interpretation here.

Target Market(s)

Electrical contractors

Industry/Entity Type

Business

Contact Information for Business Card

Logo
Name & Surname: Halyna Dorosh
Job Title: Director of Marketing
Email: halya.dorosh@quillmail.example
Cell phone: XXX.XXX.XXXX
Address: 20517 - 87 Ave. Edmonton, AB, Canada. T6K 4N8
Business Phone: 780.555.0184
Website: www.brovix.example

Font styles to use
Other font styles liked:
• Lato

Requirements
Must have
• Logo & website
Nice to have
• Brand elements - some of them you may find in the attached Brand Guidelines (e.g. three lines on the background signifying "W")

```html
<!DOCTYPE html>
<html lang="en">
<head>
<meta charset="utf-8">
<title>Brovix business cards</title>
<link href="https://fonts.googleapis.com/css2?family=Lato:wght@400;700&display=swap" rel="stylesheet">
<style>
  :root {
    --brand-green: #8dc63f;
    --brand-grey: #525356;
    --ink: #4a4b4d;
    --ink-soft: #6d6e71;
    --paper: #ffffff;
    --backdrop: #ececea;
  }
  * { box-sizing: border-box; margin: 0; padding: 0; }
  html, body { width: 1200px; height: 1000px; overflow: hidden; }
  body {
    background: var(--backdrop);
    font-family: "Lato", sans-serif;
    color: var(--ink);
    position: relative;
  }
  .card {
    position: absolute;
    box-shadow: 0 4px 14px rgba(0,0,0,0.18);
  }
  .card--rounded { border-radius: 30px; }
  .card--front { background: var(--brand-grey); }
  .card--back { background: var(--paper); }

  .front-left  { left: 64px;  top: 60px;  width: 508px; height: 290px; }
  .back-left   { left: 64px;  top: 428px; width: 508px; height: 288px; }
  .front-right { left: 624px; top: 283px; width: 512px; height: 292px; }
  .back-right  { left: 624px; top: 640px; width: 512px; height: 292px; }

  .wordmark {
    position: absolute;
    left: 0; right: 0; top: 50%;
    transform: translateY(-50%);
    display: flex; align-items: center; justify-content: center; gap: 14px;
    color: var(--brand-green);
    font-size: 66px;
    font-weight: 400;
    line-height: 1;
  }
  .wordmark__square { width: 40px; height: 40px; background: var(--brand-green); }

  .holder__name { position: absolute; left: 27px; top: 82px; font-size: 25px; color: var(--ink); }
  .holder__title { position: absolute; left: 27px; top: 115px; font-size: 14.5px; color: var(--ink-soft); }
  .holder__rule { position: absolute; left: 27px; right: 31px; top: 142px; height: 2px; background: var(--ink-soft); }

  .address {
    position: absolute; right: 31px; top: 148px;
    font-size: 15px; line-height: 20px; color: var(--ink-soft); text-align: right;
  }
  .address__line { display: flex; justify-content: flex-end; align-items: center; gap: 14px; }
  .address svg { width: 12px; height: 14px; fill: var(--ink); }

  .contacts { position: absolute; left: 27px; top: 194px; list-style: none; }
  .contacts li { display: flex; align-items: center; height: 23px; font-size: 17px; color: var(--ink); }
  .contacts svg { width: 13px; height: 13px; fill: var(--ink); margin-right: 13px; }

  .mini-mark {
    position: absolute; right: 31px; top: 204px;
    display: flex; align-items: center; gap: 7px;
    font-size: 30px; line-height: 1; color: var(--ink);
  }
  .mini-mark__square { width: 18px; height: 18px; background: var(--brand-green); }
  .website { position: absolute; right: 31px; top: 241px; font-size: 14px; color: var(--ink-soft); }
</style>
</head>
<body>

  <div class="card card--front card--rounded front-left">
    <div class="wordmark"><span class="wordmark__square"></span>brovix</div>
  </div>

  <div class="card card--back card--rounded back-left">
    <p class="holder__name">Halyna Dorosh</p>
    <p class="holder__title">Director of Marketing</p>
    <div class="holder__rule"></div>
    <div class="address">
      <div class="address__line"><svg viewBox="0 0 12 14"><path d="M6 0a5 5 0 0 0-5 5c0 3.5 5 9 5 9s5-5.5 5-9a5 5 0 0 0-5-5zm0 7a2 2 0 1 1 0-4 2 2 0 0 1 0 4z"/></svg>20517 - 87 Ave. Edmonton</div>
      <div>AB, Canada. T6K 4N8</div>
    </div>
    <ul class="contacts">
      <li><svg viewBox="0 0 13 13"><path d="M3 0l2 3-1.3 1.5a8 8 0 0 0 4.8 4.8L10 8l3 2-1 2.5C6 13 0 7 .5 1z"/></svg>XXX.XXX.XXXX</li>
      <li><svg viewBox="0 0 13 13"><path d="M1 3c3-3 8-3 11 0v2H9V3.5H4V5H1zM3 6h7l2 6H1zm3.5 1.5a2 2 0 1 0 0 4 2 2 0 0 0 0-4z"/></svg>780.555.0184</li>
      <li><svg viewBox="0 0 13 13"><path d="M1 3h11v1L6.5 7.5 1 4zm0 2.2l5.5 3.5L12 5.2V11H1z"/></svg>halya.dorosh@quillmail.example</li>
    </ul>
    <div class="mini-mark"><span class="mini-mark__square"></span>brovix</div>
    <p class="website">www.brovix.example</p>
  </div>

  <div class="card card--front front-right">
    <div class="wordmark"><span class="wordmark__square"></span>brovix</div>
  </div>

  <div class="card card--back back-right">
    <p class="holder__name">Halyna Dorosh</p>
    <p class="holder__title">Director of Marketing</p>
    <div class="holder__rule"></div>
    <div class="address">
      <div class="address__line"><svg viewBox="0 0 12 14"><path d="M6 0a5 5 0 0 0-5 5c0 3.5 5 9 5 9s5-5.5 5-9a5 5 0 0 0-5-5zm0 7a2 2 0 1 1 0-4 2 2 0 0 1 0 4z"/></svg>20517 - 87 Ave. Edmonton</div>
      <div>AB, Canada. T6K 4N8</div>
    </div>
    <ul class="contacts">
      <li><svg viewBox="0 0 13 13"><path d="M3 0l2 3-1.3 1.5a8 8 0 0 0 4.8 4.8L10 8l3 2-1 2.5C6 13 0 7 .5 1z"/></svg>XXX.XXX.XXXX</li>
      <li><svg viewBox="0 0 13 13"><path d="M1 3c3-3 8-3 11 0v2H9V3.5H4V5H1zM3 6h7l2 6H1zm3.5 1.5a2 2 0 1 0 0 4 2 2 0 0 0 0-4z"/></svg>780.555.0184</li>
      <li><svg viewBox="0 0 13 13"><path d="M1 3h11v1L6.5 7.5 1 4zm0 2.2l5.5 3.5L12 5.2V11H1z"/></svg>halya.dorosh@quillmail.example</li>
    </ul>
    <div class="mini-mark"><span class="mini-mark__square"></span>brovix</div>
    <p class="website">www.brovix.example</p>
  </div>

</body>
</html>
```